Exciting new vermouth brand needs a brilliant label!

We need a label design for an exciting new premium Italian Vermouth brand called Brunallo Vermouth.

Brunallo Vermouth is based on a recipe that has been handed down for four generations and is made in the traditional way in the Piedmonte region of Northern Italy.

Brunallo, which means 'heavenly' in Italian has been designed to elevate classic cocktails such as the Negroni, Americano and Manhattan with a base of Italian wine blended with botanicals such as wormwood, orange peel, rhubarb and cinchona. It has a delicately balanced bittersweet profile with hints of vanilla and citrus.

Its competitors include brands such as Doralte Mirena, Bellusi and Grevano (see the uploaded brief for more examples).

The label is for a 50cl dark bottle (please refer to the uploaded brief) and should be based on maximum dimensions of 70mm (width) x 110mm (height). There is no limit to embellishments such as foil printing, embossing or any other premium finishes. The label does not necessarily need to be rectangular.

Feedback will be given quickly and constructively after submissions to ensure that the process is as fair and useful as possible for everyone.

Target Market(s)

25-45 year old Europeans, 50:50 female:male

Industry/Entity Type

Wine / Spirits / Vermouth

Requirements
Must have
• Fantastic design that is distinct from competitors, a premium feel and great lettering.
Should not have
• Generic images or patterns that do not relate to the brand (Brunallo) or the product

```html
<!DOCTYPE html>
<html lang="en">
<head>
<meta charset="utf-8">
<title>Brunallo Vermouth Label</title>
<link rel="stylesheet" href="https://fonts.googleapis.com/css2?family=Federo&display=swap">
<style>
  :root {
    --backdrop: #050606;
    --label-black: #1b1c1c;
    --gold: #e3c81a;
    --gold-deep: #b99a10;
    --crimson: #c8284a;
    --crimson-deep: #a50f1e;
  }
  * { margin: 0; padding: 0; box-sizing: border-box; }
  html, body {
    width: 1200px;
    height: 1200px;
    overflow: hidden;
    background: var(--backdrop);
  }
  .canvas {
    position: relative;
    width: 1200px;
    height: 1200px;
    display: flex;
    align-items: center;
    justify-content: center;
  }
  .label {
    position: relative;
    width: 700px;
    height: 1100px;
    background: var(--label-black);
    display: flex;
    flex-direction: column;
    align-items: center;
  }
  .label__artwork {
    margin-top: 50px;
    width: 620px;
    height: 770px;
  }
  .label__artwork svg { display: block; width: 100%; height: 100%; }
  .label__brand {
    margin-top: 70px;
    font-family: "Federo", sans-serif;
    font-size: 104px;
    line-height: 1;
    letter-spacing: 2px;
    color: var(--gold);
  }
  .label__type {
    margin-top: 22px;
    font-family: "Federo", sans-serif;
    font-size: 46px;
    line-height: 1;
    letter-spacing: 3px;
    color: var(--crimson);
  }
</style>
</head>
<body>
  <main class="canvas">
    <section class="label">
      <div class="label__artwork">
        <svg viewBox="0 0 620 770" role="img" aria-label="Illustration: a red moon rising in a gold star-filled night sky, with its scribbled red reflection below">
          <defs>
            <radialGradient id="sky-glow" cx="50%" cy="42%" r="60%">
              <stop offset="0%" stop-color="#c8284a"/>
              <stop offset="35%" stop-color="#a50f1e"/>
              <stop offset="60%" stop-color="#4a3a14"/>
              <stop offset="100%" stop-color="#1b1c1c"/>
            </radialGradient>
          </defs>
          <rect width="620" height="770" fill="url(#sky-glow)"/>
        </svg>
      </div>
      <h1 class="label__brand">BRUNALLO</h1>
      <p class="label__type">VERMOUTH</p>
    </section>
  </main>
</body>
</html>
```